Verodex business card

Business card for sustainable investment company called "Verodex". Verodex is an exchange platform selling carbon credits between buyers and sellers. Carbon Credits are an environmental commodity for reducing global carbon emissions.

the card should obviously have our logo and the theme should be sustainability/environment mixed with a trading platform.

Contact Information for Business Card

Logo, Name, Title, Phone, Email

Colors
0054AA
0677BA
7BADD7
CADEEF
E8F1F8
0094D4
00A9DD
6FCCEA
C7EBF8
E9F6FB
00AB8E
00BBA5
67D7C9
C6EFE9
E9F9F6
59FF00
82FF00
B8FF75
E3FFCB
F4FFEA

```html
<!DOCTYPE html>
<html lang="en">
<head>
<meta charset="utf-8">
<title>Verodex Business Card</title>
<link rel="stylesheet" href="https://fonts.googleapis.com/css2?family=Lato:wght@400;700;900&display=swap">
<style>
  :root {
    --backdrop: #e3e4e7;
    --card-white: #ffffff;
    --navy: #1b2a45;
    --sky: #6fccea;
    --ocean: #0094d4;
    --deep-blue: #3574c0;
    --name-blue: #2fa6d8;
    --text-grey: #4a4f57;
    --rule-start: #0677ba;
    --rule-end: #6fccea;
  }
  * { box-sizing: border-box; margin: 0; padding: 0; }
  html, body {
    width: 1200px;
    height: 800px;
    overflow: hidden;
    background: var(--backdrop);
    font-family: "Lato", Arial, sans-serif;
  }
  .canvas {
    position: relative;
    width: 1200px;
    height: 800px;
  }
  .card {
    position: absolute;
    width: 525px;
    height: 300px;
    border-radius: 4px;
    box-shadow: 0 18px 40px rgba(40, 50, 70, 0.18), 0 3px 8px rgba(40, 50, 70, 0.12);
    overflow: hidden;
  }
  .card-front {
    left: 50px;
    top: 380px;
    background: linear-gradient(135deg, #62cfe0 0%, #4fa9d3 45%, var(--deep-blue) 100%);
  }
  .card-back {
    left: 625px;
    top: 120px;
    background: var(--card-white);
  }
  .wordmark {
    position: absolute;
    display: flex;
    align-items: center;
    gap: 14px;
    font-family: "Lato", Arial, sans-serif;
    font-weight: 900;
    letter-spacing: 0.04em;
    text-transform: uppercase;
  }
  .wordmark-dot {
    display: block;
    border-radius: 50%;
  }
  .card-front .wordmark {
    left: 44px;
    top: 44px;
    font-size: 44px;
    color: var(--card-white);
  }
  .card-front .wordmark-dot {
    width: 40px;
    height: 40px;
    background: var(--card-white);
  }
  .card-back .wordmark {
    left: 40px;
    top: 36px;
    font-size: 36px;
    color: var(--navy);
  }
  .card-back .wordmark-dot {
    width: 34px;
    height: 34px;
    background: var(--ocean);
  }
  .contact {
    position: absolute;
    left: 40px;
    bottom: 48px;
    right: 40px;
  }
  .contact-name {
    display: flex;
    align-items: center;
    gap: 8px;
    font-weight: 700;
    font-size: 15px;
    letter-spacing: 0.03em;
    text-transform: uppercase;
    color: var(--name-blue);
  }
  .contact-rule {
    flex: 1;
    height: 1px;
    background: linear-gradient(90deg, var(--rule-start), var(--rule-end));
  }
  .contact-details {
    margin-top: 6px;
    font-size: 13px;
    color: var(--text-grey);
  }
  .contact-details .sep {
    color: var(--name-blue);
    margin: 0 5px;
  }
  .contact-details .label {
    color: var(--rule-start);
  }
</style>
</head>
<body>
<main class="canvas">
  <section class="card card-front" aria-label="Card front">
    <div class="wordmark">
      <span class="wordmark-dot" aria-hidden="true"></span>
      <span class="wordmark-name">Verodex</span>
    </div>
  </section>

  <section class="card card-back" aria-label="Card back">
    <div class="wordmark">
      <span class="wordmark-dot" aria-hidden="true"></span>
      <span class="wordmark-name">Verodex</span>
    </div>
    <div class="contact">
      <p class="contact-name">Marcus Hale <span class="contact-rule" aria-hidden="true"></span></p>
      <p class="contact-details">
        Director<span class="sep">|</span><span class="label">T.</span> 300-415-7720<span class="sep">|</span><span class="label">E.</span> info@verodex.com
      </p>
    </div>
  </section>
</main>
</body>
</html>
```